Redesign a Start-Up Dating Website

Website: https://morvelique.com.
Make sure the design has an island style theme.
I would like the 7 pages of my website to have a new and professional look. I want the same colors to remain, but I want a creative look for all the pages. This is a dating website that is in the startup stage. So, I want to give my entire website a custom makeover. I want something that will stand out from the other dating sites. Something that will attract more people to want to use my services, and hopefully get new members.
Target Market(s)
Dating
Industry/Entity Type
Dating
Coding
Coded - Design and coding required
Number of Pages Required
5+ page
Font styles to use
Other font styles liked:
- Decorative, San Serif
Requirements
Must have
- The design must have the original colors and a stylish font to go along. The design must be creative, welcoming, and professional. I would like an island style theme for the website. This is a dating website so make sure that the design is tailored to that aspect.
Nice to have
- It would be nice to have a decorative font and a professional style on all the pages. Make sure the design will be mobile responsive and friendly for all the pages on the website.
Should not have
- The design should not be bland and uncreative.

```html
<!DOCTYPE html>
<html lang="en">
<head>
<meta charset="utf-8">
<title>Morvelique – Dating Made Easy</title>
<link href="https://fonts.googleapis.com/css2?family=Lobster&family=Open+Sans:ital,wght@0,400;0,600;0,700;1,400&display=swap" rel="stylesheet">
<style>
:root{
  --purple:#6c3fa3;
  --purple-dark:#52307f;
  --orange:#f5a11c;
  --orange-dark:#e58a0e;
  --teal:#3dbb9f;
  --teal-dark:#2a9a84;
  --ink:#333;
  --muted:#8a8a8a;
  --line:#e2e2e2;
  --footer:#1e1e1e;
  --footer-bar:#141414;
  --white:#fff;
}
*{box-sizing:border-box;margin:0;padding:0}
html,body{width:1200px;height:2736px;overflow:hidden}
body{font-family:"Open Sans",sans-serif;color:var(--ink);background:var(--white)}
.script{font-family:"Lobster",cursive;font-weight:400}

/* header */
.site-header{height:112px;display:flex;align-items:center;padding:0 60px;border-bottom:1px solid var(--line)}
.brand{display:flex;align-items:center;gap:14px;font-family:"Lobster",cursive;font-size:40px;color:var(--purple)}
.brand-dot{width:34px;height:34px;border-radius:50%;background:var(--orange)}
.main-nav{margin-left:auto;display:flex;gap:34px;font-size:15px;font-weight:600;color:#666}
.main-nav a{color:inherit;text-decoration:none;padding-bottom:6px}
.main-nav a.active{color:var(--purple);border-bottom:3px solid var(--purple)}
.auth{display:flex;gap:12px;margin-left:40px}
.btn{display:inline-block;border-radius:4px;color:var(--white);font-weight:700;font-size:15px;padding:10px 20px;text-decoration:none}
.btn-login{background:var(--purple)}
.btn-register{background:var(--orange)}

/* hero */
.hero{height:508px;position:relative;background:linear-gradient(100deg,#6e5a45 0%,#b89060 35%,#e3b57a 55%,#9a7654 80%,#5a4634 100%);color:var(--white)}
.hero-photo{position:absolute;inset:0}
.hero-text{position:absolute;left:96px;top:90px}
.hero-title{font-size:84px;text-shadow:0 2px 6px rgba(0,0,0,.25)}
.hero-rule{margin:10px 0 26px;width:260px;height:20px}
.hero-lines p{font-family:"Lobster",cursive;font-size:22px;margin-bottom:22px;color:#fff7d6}
.hero-lines p:last-child{color:#f7d46a}
.hero-dots{display:flex;gap:8px;margin-top:10px}
.hero-dots span{width:12px;height:12px;border-radius:50%;border:2px solid var(--white)}
.hero-dots span:first-child{background:var(--white)}

/* steps */
.steps{height:580px;text-align:center;padding-top:50px}
.section-title{font-size:58px;color:var(--orange)}
.section-title em{font-style:normal;color:var(--purple)}
.title-rule{width:520px;height:3px;margin:20px auto 26px;background:linear-gradient(90deg,transparent,var(--orange),transparent)}
.lead{font-size:15px;color:#555;line-height:26px}
.step-row{display:flex;justify-content:center;gap:190px;margin-top:62px}
.step{width:220px}
.step-img{width:140px;height:140px;border-radius:50%;margin:0 auto;border:6px solid var(--white);box-shadow:0 0 0 3px var(--teal)}
.step h3{font-family:"Lobster",cursive;font-weight:400;font-size:24px;color:var(--purple);margin:22px 0 12px}
.step p{font-size:13px;color:var(--muted);line-height:21px}

/* benefits */
.benefits{height:568px;background:linear-gradient(180deg,var(--teal),var(--teal-dark));text-align:center;color:var(--white);padding-top:54px}
.benefits .section-title{color:var(--white);font-size:56px}
.benefits .title-rule{background:linear-gradient(90deg,transparent,var(--white),transparent);margin:14px auto 18px;width:380px}
.benefits .lead{color:#e9fffa;font-style:italic}
.member-row{display:flex;justify-content:center;gap:76px;margin-top:46px}
.member-img{width:136px;height:136px;border-radius:50%;border:5px solid var(--white);margin:0 auto}
.member h4{font-family:"Lobster",cursive;font-weight:400;font-size:22px;margin-top:16px}
.member span{font-size:13px;color:#e9fffa}
.btn-plans{margin-top:34px;background:var(--orange);padding:14px 34px;border-radius:30px;font-size:17px}

/* search */
.search-area{height:652px;display:flex;gap:54px;padding:60px 100px 0}
.feature-photo{width:580px;height:520px;background:linear-gradient(135deg,#7b5aa8,#b799d8 55%,#8d6fb8);border:8px solid #f1ebf8;box-shadow:0 0 0 1px #d8cde6;position:relative}
.play{position:absolute;left:50%;top:50%;width:72px;height:72px;margin:-36px;border-radius:50%;border:4px solid var(--white);display:flex;align-items:center;justify-content:center}
.quick-search{width:366px;border-left:2px dashed #cbbbe0;border-right:2px dashed #cbbbe0;padding:0 34px}
.quick-search h2{font-size:42px;color:var(--purple);text-align:center;font-style:italic}
.quick-search .sub{text-align:center;font-size:12px;color:var(--muted);margin:6px 0 26px}
.field{margin-bottom:22px}
.field label{display:block;font-size:11px;font-weight:700;color:#777;margin-bottom:6px;letter-spacing:.5px}
.select{height:40px;border:1px solid #ddd;border-radius:3px;display:flex;align-items:center;justify-content:flex-end;padding-right:12px}
.btn-search{display:block;width:100%;text-align:center;background:var(--purple);padding:12px;font-size:17px;margin-top:12px}

/* footer */
.site-footer{height:276px;background:var(--footer);color:#bbb;position:relative}
.footer-cols{display:flex;padding:36px 100px 0;gap:90px}
.footer-cols h5{color:var(--white);font-size:15px;margin-bottom:18px;letter-spacing:.5px}
.about{width:420px;font-size:13px;line-height:22px}
.about a{color:var(--orange);font-weight:600;text-decoration:none}
.links{display:grid;grid-template-columns:130px 130px;gap:8px 0;font-size:13px}
.contact li{list-style:none;font-size:13px;margin-bottom:10px;display:flex;align-items:center;gap:10px}
.social{display:flex;gap:10px;margin-top:14px}
.social span{width:26px;height:26px;border-radius:50%;background:#3a3a3a}
.footer-bar{position:absolute;left:0;right:0;bottom:0;height:50px;background:var(--footer-bar);font-size:12px;display:flex;align-items:center;padding:0 100px;color:#888}
</style>
</head>
<body>

<header class="site-header">
  <div class="brand"><span class="brand-dot"></span>Morvelique</div>
  <nav class="main-nav">
    <a class="active" href="#">Home</a><a href="#">Search</a><a href="#">Members</a><a href="#">Extras</a><a href="#">About</a><a href="#">Premium</a><a href="#">Contact</a>
  </nav>
  <div class="auth"><a class="btn btn-login" href="#">Login</a><a class="btn btn-register" href="#">Register</a></div>
</header>

<section class="hero">
  <div class="hero-photo" role="img" aria-label="Couple embracing at sunset on an island beach"></div>
  <div class="hero-text">
    <h1 class="hero-title script">Morvelique</h1>
    <svg class="hero-rule" viewBox="0 0 260 20"><line x1="10" y1="10" x2="250" y2="10" stroke="#fff" stroke-width="2"/><circle cx="10" cy="10" r="4" fill="#fff"/><path d="M250 10l-10-6v12z" fill="#fff"/></svg>
    <div class="hero-lines">
      <p>Let's Find Your Perfect Match Today</p>
      <p>Find Your Perfect Match For Free!</p>
      <p>Online Dating Made Easy On morvelique.com</p>
    </div>
    <div class="hero-dots"><span></span><span></span><span></span><span></span></div>
  </div>
</section>

<section class="steps">
  <h2 class="section-title script">Dating is <em>Easy</em> with Morvelique</h2>
  <div class="title-rule"></div>
  <p class="lead">Sign Up For 30 Days Free Trial<br>Enjoy All The Benefits Morvelique Has To Offer With A Full Membership</p>
  <div class="step-row">
    <div class="step">
      <div class="step-img" role="img" aria-label="Smiling woman creating a profile" style="background:linear-gradient(135deg,#3a6f72,#9cc7b8)"></div>
      <h3>Create a Profile</h3>
      <p>Let people know all about you, the good and the quirky, share the world your island calls home with a photo or two.</p>
    </div>
    <div class="step">
      <div class="step-img" role="img" aria-label="Man browsing matches" style="background:linear-gradient(135deg,#5c6b78,#c6c1b6)"></div>
      <h3>Find Matches</h3>
      <p>Browse other users and feel the excitement of getting your first message and getting to know potential dates.</p>
    </div>
    <div class="step">
      <div class="step-img" role="img" aria-label="Couple on a first date" style="background:linear-gradient(135deg,#b08a63,#e8d2b4)"></div>
      <h3>Start Dating</h3>
      <p>Once you've found your potential soulmate, it's time to meet up and see if this is the start of your journey together.</p>
    </div>
  </div>
</section>

<section class="benefits">
  <h2 class="section-title script">Benefits</h2>
  <div class="title-rule"></div>
  <p class="lead">Affordable Long Stays, Not Just One-Night Getaways</p>
  <div class="member-row">
    <div class="member"><div class="member-img" role="img" aria-label="Member portrait" style="background:linear-gradient(135deg,#8a5b3c,#d9a57c)"></div><h4>Lorem dolor sit</h4><span>23 years old</span></div>
    <div class="member"><div class="member-img" role="img" aria-label="Member portrait" style="background:linear-gradient(135deg,#6b6b6b,#c4b5a5)"></div><h4>Lorem dolor sit</h4><span>25 years old</span></div>
    <div class="member"><div class="member-img" role="img" aria-label="Member portrait" style="background:linear-gradient(135deg,#5a3d2e,#c9a08a)"></div><h4>Lorem dolor sit</h4><span>22 years old</span></div>
    <div class="member"><div class="member-img" role="img" aria-label="Member portrait" style="background:linear-gradient(135deg,#4a3326,#a77a5c)"></div><h4>Lorem dolor sit</h4><span>27 years old</span></div>
    <div class="member"><div class="member-img" role="img" aria-label="Member portrait" style="background:linear-gradient(135deg,#9a6a4a,#e7c1a0)"></div><h4>Lorem dolor sit</h4><span>24 years old</span></div>
  </div>
  <a class="btn btn-plans" href="#">View Membership Plans</a>
</section>

<section class="search-area">
  <div class="feature-photo" role="img" aria-label="Happy couple relaxing together, video preview">
    <div class="play"><svg width="26" height="28" viewBox="0 0 26 28"><path d="M4 2l20 12L4 26z" fill="#fff"/></svg></div>
  </div>
  <div class="quick-search">
    <h2 class="script">Quick search</h2>
    <p class="sub">Enter your details below and meet your match</p>
    <div class="field"><label>I AM</label><div class="select"><svg width="10" height="6"><path d="M0 0h10L5 6z" fill="#999"/></svg></div></div>
    <div class="field"><label>SEEKING A</label><div class="select"><svg width="10" height="6"><path d="M0 0h10L5 6z" fill="#999"/></svg></div></div>
    <div class="field"><label>AGE</label><div class="select"><svg width="10" height="6"><path d="M0 0h10L5 6z" fill="#999"/></svg></div></div>
    <div class="field"><label>TO</label><div class="select"><svg width="10" height="6"><path d="M0 0h10L5 6z" fill="#999"/></svg></div></div>
    <div class="field"><label>COUNTRY</label><div class="select"><svg width="10" height="6"><path d="M0 0h10L5 6z" fill="#999"/></svg></div></div>
    <a class="btn btn-search" href="#">Search</a>
  </div>
</section>

<footer class="site-footer">
  <div class="footer-cols">
    <div class="about">
      <h5>ABOUT</h5>
      <p>Morvelique aims to provide a straight forward way to use online dating services which uses simple, friendly tools to widen the network of people you are able to talk with and meet.</p>
      <a href="#">Read More</a>
    </div>
    <div>
      <h5>QUICK LINKS</h5>
      <div class="links"><span>Morvelique</span><span>Members</span><span>About</span><span>Premium</span><span>Contact</span><span>Register</span><span>Login</span><span>Search</span></div>
    </div>
    <div>
      <h5>CONTACT US</h5>
      <ul class="contact">
        <li><svg width="12" height="16" viewBox="0 0 12 16"><path d="M6 0a6 6 0 0 0-6 6c0 4.5 6 10 6 10s6-5.5 6-10a6 6 0 0 0-6-6zm0 8.5A2.5 2.5 0 1 1 6 3.5a2.5 2.5 0 0 1 0 5z" fill="#f5a11c"/></svg>Morvelique Dating</li>
        <li><svg width="14" height="14" viewBox="0 0 14 14"><path d="M3 0l3 3-2 2c1 2 3 4 5 5l2-2 3 3-2 3C6 14 0 8 0 3z" fill="#f5a11c"/></svg>(555) 014-2290</li>
        <li><svg width="14" height="10" viewBox="0 0 14 10"><rect width="14" height="10" rx="1" fill="#f5a11c"/><path d="M0 0l7 6 7-6" stroke="#1e1e1e" fill="none"/></svg>hello@morvelique.com</li>
      </ul>
      <div class="social"><span></span><span></span><span></span><span></span><span></span></div>
    </div>
  </div>
  <div class="footer-bar">Copyright © Morvelique 2017 - All rights reserved</div>
</footer>

</body>
</html>
```